Birchline Septic Solutions

Would like to see some single sided ones but would also like to see some double sided with one sided only being the logo. Owners name is Colin Vandro. Phone number is 555-214-0387
Services are pumping, inspections, installs, and repairs

Contact Information for Business Card

555-241-0387 Colin Vandro Brookhaven, OH

```html
<!DOCTYPE html>
<html lang="en">
<head>
<meta charset="utf-8">
<title>Birchline Septic Solutions – Business Card</title>
<link href="https://fonts.googleapis.com/css2?family=Barlow:ital,wght@0,300;0,400;0,600;0,700;1,700&family=Poppins:wght@300;400;600&display=swap" rel="stylesheet">
<style>
  :root {
    --page-bg: #2a2b2d;
    --card-bg: #141414;
    --card-pattern: #1c1c1d;
    --teal: #3ec6c0;
    --white: #f4f4f4;
    --muted: #d8d8d8;
  }
  * { box-sizing: border-box; margin: 0; padding: 0; }
  html, body {
    width: 1200px; height: 900px; overflow: hidden;
    background: var(--page-bg);
  }
  .sheet { position: relative; width: 1200px; height: 900px; }
  .card {
    position: absolute; left: 250px; width: 700px; height: 400px;
    background: var(--card-bg);
    border: 2px solid var(--teal);
    border-radius: 4px;
    overflow: hidden;
    box-shadow: 0 14px 30px rgba(0,0,0,.45);
  }
  .card--front { top: 30px; }
  .card--back { top: 470px; }

  .holder { position: absolute; left: 52px; top: 58px; }
  .holder__name {
    font-family: "Barlow", sans-serif; font-weight: 700; font-style: italic;
    font-size: 30px; letter-spacing: .5px; text-transform: uppercase;
    color: var(--teal); line-height: 1;
  }
  .holder__title {
    font-family: "Poppins", sans-serif; font-weight: 300;
    font-size: 17px; color: var(--muted); margin-top: 6px;
  }

  .brand-name {
    font-family: "Poppins", sans-serif; font-weight: 600;
    color: var(--white); text-transform: uppercase;
    letter-spacing: 3px; line-height: 1.15;
  }
  .card--front .brand-name {
    position: absolute; right: 50px; top: 120px;
    font-size: 28px; text-align: right;
  }

  .contact {
    position: absolute; left: 260px; top: 250px;
    list-style: none;
    font-family: "Poppins", sans-serif; font-weight: 400;
    font-size: 17px; color: var(--white);
  }
  .contact__item { display: flex; align-items: center; gap: 10px; height: 28px; white-space: nowrap; }
  .contact__icon { width: 15px; height: 15px; flex: none; }

  .back-pattern {
    position: absolute; inset: 0;
    background: repeating-linear-gradient(-25deg, var(--card-bg) 0 34px, var(--card-pattern) 34px 68px);
  }
  .card--back .brand-name {
    position: absolute; right: 40px; bottom: 36px;
    font-size: 20px; text-align: right;
  }
</style>
</head>
<body>
<main class="sheet">

  <section class="card card--front" aria-label="Business card front">
    <div class="holder">
      <p class="holder__name">Colin Vandro</p>
      <p class="holder__title">Founder / CEO</p>
    </div>

    <p class="brand-name">Birchline<br>Septic Solutions</p>

    <ul class="contact">
      <li class="contact__item">
        <svg class="contact__icon" viewBox="0 0 16 16" aria-hidden="true"><path fill="var(--teal)" d="M3.5 1l2.5 3-1.5 1.6c.8 2 2.3 3.6 4.4 4.4L10.5 8.5l3 2.5-1.4 2.8C6.5 13.5 2.5 9.5 1 4z"/></svg>
        555-241-0387
      </li>
      <li class="contact__item">
        <svg class="contact__icon" viewBox="0 0 16 16" aria-hidden="true"><rect x="1" y="3" width="14" height="10" rx="1" fill="var(--teal)"/><path d="M1.5 4l6.5 5 6.5-5" stroke="var(--card-bg)" stroke-width="1.4" fill="none"/></svg>
        info@birchlineseptic.com
      </li>
      <li class="contact__item">
        <svg class="contact__icon" viewBox="0 0 16 16" aria-hidden="true"><circle cx="8" cy="8" r="7" fill="var(--teal)"/><path d="M1 8h14M8 1c-3 3.5-3 10.5 0 14M8 1c3 3.5 3 10.5 0 14" stroke="var(--card-bg)" stroke-width="1.1" fill="none"/></svg>
        www.birchlineseptic.com
      </li>
      <li class="contact__item">
        <svg class="contact__icon" viewBox="0 0 16 16" aria-hidden="true"><path fill="var(--teal)" d="M8 0.5a5.5 5.5 0 0 0-5.5 5.5c0 4 5.5 9.5 5.5 9.5s5.5-5.5 5.5-9.5A5.5 5.5 0 0 0 8 0.5z"/><circle cx="8" cy="6" r="2" fill="var(--card-bg)"/></svg>
        Brookhaven, OH
      </li>
    </ul>
  </section>

  <section class="card card--back" aria-label="Business card back">
    <div class="back-pattern" role="img" aria-label="Tone-on-tone repeated brand mark pattern across the card back"></div>
    <p class="brand-name">Birchline<br>Septic Solutions</p>
  </section>

</main>
</body>
</html>
```